Red Mo's Wine Label Project

We need a new entry level wine label called "Red Mo's" for a range of wines we are developing from inland Australia. Our company is made up of three youngish guys who live hard and love taking the mickey. Red Mo is Red Morrie - the largest and loudest of the three partners (and ideally this label will take the mickey out of him). We've grown the grapes ourselves for this first release which will be a 2012 Pinot Gris. Wine style is dry, young, fresh and contemporary and pitched at the sub AUD $10 retail price point. The package will be flint (clear) claret shape bottle with plain screwcap (colour matched to suit the winning label design).

I've attached a couple of photos of Red Morrie to give you some idea of his presence and persona.

Target Market(s)

Semi educated 25 - 40 year old wine drinkers. Skewed towards females.

Industry/Entity Type

Retail

Requirements
Should not have
• Anything traditional or old fashioned

```html
<!DOCTYPE html>
<html lang="en">
<head>
<meta charset="utf-8">
<title>Red Mo's Pinot Gris 2012 – Colour Scheme 5</title>
<link href="https://fonts.googleapis.com/css2?family=Comfortaa:wght@400;700&family=Arimo:wght@400;700&family=Tinos&display=swap" rel="stylesheet">
<style>
  :root {
    --teal-deep: #005f5f;
    --orange: #f05a0f;
    --green: #12b28e;
    --cap-teal: #0f5564;
    --sidebar-grey: #6b6866;
    --bar-grey: #706e6c;
    --band-grey: #e8e8e8;
    --white: #ffffff;
    --yellow: #f2d31b;
    --ink: #3a3a3a;
  }
  * { margin: 0; padding: 0; box-sizing: border-box; }
  html, body { width: 1200px; height: 900px; overflow: hidden; background: var(--white); }
  .board { position: relative; width: 1200px; height: 900px; background: var(--white); overflow: hidden; }

  .sidebar { position: absolute; left: 0; top: 0; width: 85px; height: 900px; background: var(--sidebar-grey); }

  .backdrop-band { position: absolute; background: var(--band-grey); }
  .backdrop-band--upper { left: 85px; top: 296px; width: 480px; height: 34px; }
  .backdrop-band--lower { left: 930px; top: 398px; width: 270px; height: 34px; }

  .label { position: absolute; left: 225px; top: 23px; width: 332px; height: 847px; background: var(--teal-deep); overflow: hidden; }
  .label__brand { position: absolute; left: 62px; top: 200px; width: 220px; }
  .label__dot { width: 26px; height: 26px; border-radius: 50%; background: var(--orange); margin-left: 72px; margin-bottom: 14px; }
  .label__name { font-family: "Comfortaa", sans-serif; font-weight: 700; font-size: 52px; line-height: 1; color: var(--white); letter-spacing: -1px; }
  .label__wine { position: absolute; left: 97px; top: 398px; font-family: "Comfortaa", sans-serif; font-weight: 700; }
  .label__title { font-size: 26px; color: var(--white); line-height: 1; }
  .label__variety { font-size: 14px; color: var(--orange); letter-spacing: 1px; margin-top: 4px; }
  .label__vintage { color: var(--green); }
  .label__footer-mark { position: absolute; left: 0; top: 600px; width: 332px; height: 247px; }
  .label__footer-dot { position: absolute; left: 103px; top: 40px; width: 24px; height: 24px; border-radius: 50%; background: var(--green); }
  .label__footer-name { position: absolute; left: 14px; top: 70px; font-family: "Comfortaa", sans-serif; font-weight: 700; font-size: 74px; line-height: 1; color: var(--orange); letter-spacing: -2px; white-space: nowrap; }
  .label__volume { position: absolute; left: 15px; top: 800px; font-family: "Tinos", serif; font-size: 16px; line-height: 19px; color: var(--white); }

  .heading-bar { position: absolute; left: 737px; top: 72px; width: 463px; height: 33px; background: var(--bar-grey); font-family: "Arimo", sans-serif; font-size: 17px; color: var(--white); padding: 8px 0 0 19px; }
  .heading-bar__accent { color: var(--yellow); }
  .heading-bar__light { font-weight: 400; }

  .bottle { position: absolute; left: 790px; top: 134px; width: 170px; height: 766px; }

  .pms { position: absolute; left: 1020px; top: 736px; width: 180px; }
  .pms__bar { height: 28px; background: var(--bar-grey); font-family: "Arimo", sans-serif; font-size: 15px; color: var(--white); padding: 6px 0 0 14px; }
  .pms__list { list-style: none; margin-top: 18px; }
  .pms__item { display: flex; align-items: center; height: 28px; font-family: "Arimo", sans-serif; font-size: 13px; color: var(--ink); }
  .pms__swatch { width: 20px; height: 20px; border-radius: 4px; margin-right: 6px; }
  .pms__swatch--orange { background: var(--orange); }
  .pms__swatch--green { background: var(--green); }
  .pms__swatch--teal { background: var(--teal-deep); }
</style>
</head>
<body>
<main class="board">
  <div class="sidebar"></div>
  <div class="backdrop-band backdrop-band--upper"></div>
  <div class="backdrop-band backdrop-band--lower"></div>

  <section class="label" aria-label="Wine label, flat artwork">
    <div class="label__brand">
      <div class="label__dot"></div>
      <div class="label__name">Red Mo's</div>
    </div>
    <div class="label__wine">
      <div class="label__title">RED MO'S</div>
      <div class="label__variety">PIGNOT GRIS <span class="label__vintage">2012</span></div>
    </div>
    <div class="label__footer-mark">
      <div class="label__footer-dot"></div>
      <div class="label__footer-name">Red Mo's</div>
    </div>
    <div class="label__volume">12% Vol.<br>750ml</div>
  </section>

  <div class="heading-bar"><strong>COLOUR</strong> <span class="heading-bar__light">SCHEME</span> <span class="heading-bar__accent">5</span></div>

  <svg class="bottle" viewBox="0 0 170 766" role="img" aria-label="Photo of a clear claret bottle with teal screwcap wearing the Red Mo's label">
    <defs>
      <linearGradient id="glass" x1="0" x2="1">
        <stop offset="0" stop-color="#cfc7b3"/>
        <stop offset="0.35" stop-color="#f3efe4"/>
        <stop offset="1" stop-color="#c9c1ab"/>
      </linearGradient>
    </defs>
    <path d="M60 60 L110 60 L112 170 C116 215 160 220 162 260 L162 740 Q162 766 140 766 L30 766 Q8 766 8 740 L8 260 C10 220 54 215 58 170 Z" fill="url(#glass)"/>
    <rect x="56" y="2" width="58" height="78" rx="4" fill="var(--cap-teal)"/>
    <rect x="20" y="272" width="126" height="322" fill="var(--teal-deep)"/>
  </svg>

  <aside class="pms">
    <div class="pms__bar"><strong>PMS</strong> VALUES</div>
    <ul class="pms__list">
      <li class="pms__item"><span class="pms__swatch pms__swatch--orange"></span>Tonemark 172</li>
      <li class="pms__item"><span class="pms__swatch pms__swatch--green"></span>Tonemark Green</li>
      <li class="pms__item"><span class="pms__swatch pms__swatch--teal"></span>Tonemark 323</li>
    </ul>
  </aside>
</main>
</body>
</html>
```